Business cards to launch an education platform

Hi,
I am looking at having new business cards designed.
I am a startup, developing a web platform for schools and university, the education world. It's an online assessment system.
I would like a card that looks classy, and that is using the colors and the font of my logo.

I have attached:
1) my logo
2) A business card that I have designed quickly so you can have all the information required in the card, but I really don't like it.
3) The font that I am using (Lato Regular) to design my web platform
4) Some screenshots of my web platform so you can have a look at the style that I have.

Target Market(s)

Major market: Education system: Schools and university
Minor markets: Business in general

Industry/Entity Type

Business

Contact Information for Business Card

Clara Fenwick
Director

M: 0437 518 902
E: clara.fenwick@amberLoomSystems.com.au

Requirements
Must have
• The colors of my logo

```html
<!DOCTYPE html>
<html lang="en">
<head>
<meta charset="utf-8">
<title>Amber Loom Systems – Business Cards</title>
<link rel="stylesheet" href="https://fonts.googleapis.com/css2?family=Lato:wght@300;400;700&display=swap">
<style>
  :root {
    --page-bg: #e9ecef;
    --card-white: #ffffff;
    --brand-blue: #1b6fb8;
    --brand-deep: #0f4f8e;
    --brand-cyan: #2bb4e6;
    --text-grey: #555b61;
    --pattern-light: #e6eef5;
    --pattern-mid: #d3e2ee;
  }
  * { box-sizing: border-box; margin: 0; padding: 0; }
  html, body {
    width: 1200px; height: 950px; overflow: hidden;
    background: var(--page-bg);
    font-family: "Lato", Arial, sans-serif;
  }
  .canvas {
    position: relative; width: 1200px; height: 950px;
    display: flex; flex-direction: column; align-items: center; justify-content: center; gap: 70px;
  }
  .card {
    position: relative; width: 580px; height: 332px;
    background: var(--card-white);
    box-shadow: 0 10px 30px rgba(0,0,0,0.15);
    overflow: hidden;
  }

  /* Front */
  .brand {
    position: absolute; left: 44px; top: 40px;
    display: flex; align-items: center; gap: 14px;
  }
  .brand-square { width: 34px; height: 34px; background: var(--brand-blue); }
  .brand-name {
    font-size: 26px; font-weight: 400; color: var(--brand-blue); letter-spacing: 1px;
  }
  .brand-rule {
    position: absolute; left: 44px; right: 44px; top: 100px;
    height: 1px; background: var(--brand-cyan); opacity: 0.7;
  }
  .contact { position: absolute; left: 44px; bottom: 62px; }
  .person-name {
    font-size: 21px; font-weight: 700; color: var(--brand-deep); letter-spacing: 0.5px;
  }
  .person-role {
    font-size: 13px; font-weight: 400; color: var(--brand-cyan); letter-spacing: 1px; margin-bottom: 14px;
  }
  .contact-line {
    display: flex; align-items: center; gap: 10px;
    font-size: 13px; font-weight: 300; color: var(--text-grey); margin-top: 6px;
  }
  .contact-line svg { width: 13px; height: 13px; flex: none; }
  .front-band { position: absolute; left: 0; bottom: 0; width: 580px; height: 44px; }
  .front-web {
    position: absolute; right: 22px; bottom: 12px;
    font-size: 14px; font-weight: 400; color: var(--card-white); letter-spacing: 0.3px;
  }

  /* Back */
  .back-pattern {
    position: absolute; inset: 0;
    background: linear-gradient(135deg, var(--pattern-light) 0%, #f7fafc 50%, var(--pattern-mid) 100%);
  }
  .back-brand {
    position: absolute; left: 50%; top: 50%; transform: translate(-50%, -60%);
    display: flex; align-items: center; gap: 14px;
  }
  .back-brand .brand-square { width: 44px; height: 44px; }
  .back-brand .brand-name { font-size: 32px; }
  .back-web {
    position: absolute; left: 0; right: 0; bottom: 34px; text-align: center;
    font-size: 14px; font-weight: 400; color: var(--brand-deep); letter-spacing: 0.5px;
  }
</style>
</head>
<body>
<main class="canvas">

  <section class="card card-front" aria-label="Business card front">
    <div class="brand">
      <span class="brand-square"></span>
      <span class="brand-name">Amber Loom Systems</span>
    </div>
    <div class="brand-rule"></div>

    <div class="contact">
      <p class="person-name">CLARA FENWICK</p>
      <p class="person-role">DIRECTOR</p>
      <p class="contact-line">
        <svg viewBox="0 0 13 13" aria-hidden="true"><rect x="3" y="0.5" width="7" height="12" rx="1.2" fill="none" stroke="#555b61" stroke-width="1.1"/><circle cx="6.5" cy="10.5" r="0.8" fill="#555b61"/></svg>
        0437 518 902
      </p>
      <p class="contact-line">
        <svg viewBox="0 0 13 13" aria-hidden="true"><rect x="0.5" y="2.5" width="12" height="8" fill="none" stroke="#555b61" stroke-width="1.1"/><path d="M0.5 2.5 L6.5 7 L12.5 2.5" fill="none" stroke="#555b61" stroke-width="1.1"/></svg>
        clara.fenwick@amberLoomSystems.com.au
      </p>
    </div>

    <svg class="front-band" viewBox="0 0 580 44" aria-hidden="true">
      <rect x="0" y="34" width="580" height="10" fill="var(--brand-deep)"/>
      <polygon points="200,34 320,34 312,44 192,44" fill="var(--brand-cyan)"/>
      <polygon points="340,0 580,0 580,44 310,44" fill="var(--brand-blue)"/>
    </svg>
    <span class="front-web">amberLoomSystems.com.au</span>
  </section>

  <section class="card card-back" aria-label="Business card back">
    <div class="back-pattern" role="img" aria-label="Faint repeating brand pattern in pale blue tones"></div>
    <div class="back-brand">
      <span class="brand-square"></span>
      <span class="brand-name">Amber Loom Systems</span>
    </div>
    <p class="back-web">www.amberLoomSystems.com.au</p>
  </section>

</main>
</body>
</html>
```